Business card design for a dynamic IT consulting company

We need a business card design for a young firm, specialized in the Telecommunications/Consulting industry. The name of the company is Quindor and Partners Business Consulting Ltd. (Short name: Quindor and Partnes)
Quindor = solve read reverse, so we aim to be uncomplicated and solution-oriented. The small pipe in our logo is also related to the word solve. So we need a new business card design, which is simple, eye catching and something non traditional (I would probably prefer a square shaped design rather than a rectangle, but open for suggestions). Attached our logo.

Target Market(s)

Usually our customers are Tier1 Telecoms providers (Q-Netra, Palorix, etc) and their executives.

Industry/Entity Type

Business

Contact Information for Business Card

Name: Bence Tolnavari
Email: b.tolnavari@quindor.hu
Web: www.quindor.hu
Mobile: +36 30 518 2769
Title: Managing Director

Optional:
Company name: Quindor and Partners Ltd.
Address: 1087 Budapest, Tolvenka str. 28/C, Hungary

Font styles to use
Other font styles liked:
• helveticaneue_medium, Prime Regular are used now.

Colors

Designer to choose colors to be used in the design.

Requirements
Must have
• I would like to have a 2 sided design.
Nice to have
• I thought if we make the logo a bit bigger (without the company name), that could go to the back with the company name below. I though, if the pipe in the logo is somehow touchable on the business card, would be nice and unique.

```html
<!DOCTYPE html>
<html lang="en">
<head>
<meta charset="utf-8">
<title>Quindor and Partners – Business Card</title>
<link rel="stylesheet" href="https://fonts.googleapis.com/css2?family=Dosis:wght@500;600&family=Arimo:wght@400;700&display=swap">
<style>
  :root {
    --magenta: #b5338f;
    --blue: #1a9bd7;
    --grey: #5c5d60;
    --ink: #3c3d40;
    --card: #ffffff;
    --backdrop: #e6e7ea;
  }
  * { box-sizing: border-box; margin: 0; padding: 0; }
  html, body { width: 1200px; height: 880px; overflow: hidden; }
  body {
    background: var(--backdrop);
    font-family: "Arimo", Arial, sans-serif;
    color: var(--ink);
  }
  .canvas { position: relative; width: 1200px; height: 880px; }
  .card {
    position: absolute;
    left: 240px;
    width: 720px;
    height: 400px;
    background: var(--card);
    border-radius: 26px;
    overflow: hidden;
    box-shadow: 0 6px 18px rgba(0,0,0,0.12);
  }
  .card--front { top: 20px; }
  .card--back { top: 460px; }

  /* Front */
  .front-pattern-area {
    position: absolute;
    left: 0; top: 0;
    width: 330px; height: 400px;
    background: linear-gradient(135deg, rgba(181,51,143,0.35) 0%, rgba(26,155,215,0.35) 50%, rgba(92,93,96,0.3) 100%);
  }
  .front-wordmark {
    position: absolute;
    right: 50px; bottom: 70px;
    font-family: "Dosis", "Arial Rounded MT Bold", sans-serif;
    font-weight: 500;
    font-size: 46px;
    color: var(--grey);
    letter-spacing: 0.5px;
  }

  /* Back */
  .rule { position: absolute; left: 60px; width: 620px; height: 1.5px;
    background: linear-gradient(90deg, var(--magenta) 0%, var(--magenta) 50%, var(--blue) 50%, var(--blue) 100%); }
  .rule--top { top: 100px; }
  .rule--bottom { top: 292px; }
  .brand-mark {
    position: absolute; left: 90px; top: 176px;
    display: flex; align-items: center; gap: 12px;
    font-family: "Dosis", "Arial Rounded MT Bold", sans-serif;
    font-weight: 500; font-size: 34px; color: var(--grey);
  }
  .brand-mark__square { width: 20px; height: 20px; background: var(--magenta); }
  .divider { position: absolute; left: 375px; top: 125px; width: 1.5px; height: 145px; background: var(--magenta); }
  .contact { position: absolute; left: 405px; top: 126px; }
  .contact__name {
    font-family: "Dosis", "Arial Rounded MT Bold", sans-serif;
    font-weight: 600; font-size: 26px; color: var(--ink); line-height: 1.1;
  }
  .contact__title { font-size: 16px; color: var(--magenta); margin-top: 2px; }
  .contact__list { list-style: none; margin-top: 12px; }
  .contact__item { display: flex; align-items: center; gap: 10px; font-size: 15px; color: var(--ink); margin-bottom: 6px; }
  .contact__icon { width: 18px; height: 18px; flex: none; }
  .company { position: absolute; left: 0; right: 0; top: 312px; text-align: center; }
  .company__name {
    font-family: "Dosis", "Arial Rounded MT Bold", sans-serif;
    font-weight: 600; font-size: 22px; color: var(--ink);
  }
  .company__address { font-size: 15px; color: var(--ink); margin-top: 4px; }
</style>
</head>
<body>
<main class="canvas">
  <section class="card card--front" aria-label="Card front">
    <div class="front-pattern-area" role="img" aria-label="Decorative field of magenta, blue and grey squares echoing the company symbol"></div>
    <div class="front-wordmark">Quindor &amp; Partners</div>
  </section>

  <section class="card card--back" aria-label="Card back">
    <div class="rule rule--top"></div>
    <div class="brand-mark"><span class="brand-mark__square"></span>Quindor</div>
    <div class="divider"></div>
    <div class="contact">
      <div class="contact__name">Bence Tolnavari</div>
      <div class="contact__title">Managing Director</div>
      <ul class="contact__list">
        <li class="contact__item">
          <svg class="contact__icon" viewBox="0 0 18 18" aria-hidden="true">
            <rect width="18" height="18" fill="var(--magenta)"/>
            <rect x="5" y="3" width="8" height="12" rx="1.5" fill="none" stroke="#fff" stroke-width="1.5"/>
            <circle cx="9" cy="12.5" r="0.9" fill="#fff"/>
          </svg>+36 30 518 2769</li>
        <li class="contact__item">
          <svg class="contact__icon" viewBox="0 0 18 18" aria-hidden="true">
            <rect width="18" height="18" fill="var(--grey)"/>
            <rect x="3.5" y="5" width="11" height="8" fill="none" stroke="#fff" stroke-width="1.3"/>
            <path d="M3.5 5 L9 10 L14.5 5" fill="none" stroke="#fff" stroke-width="1.3"/>
          </svg>b.tolnavari@quindor.hu</li>
        <li class="contact__item">
          <svg class="contact__icon" viewBox="0 0 18 18" aria-hidden="true">
            <rect width="18" height="18" fill="var(--blue)"/>
            <circle cx="9" cy="9" r="5.5" fill="none" stroke="#fff" stroke-width="1.2"/>
            <ellipse cx="9" cy="9" rx="2.3" ry="5.5" fill="none" stroke="#fff" stroke-width="1"/>
            <line x1="3.5" y1="9" x2="14.5" y2="9" stroke="#fff" stroke-width="1"/>
          </svg>www.quindor.hu</li>
      </ul>
    </div>
    <div class="rule rule--bottom"></div>
    <div class="company">
      <div class="company__name">Quindor and Partners Ltd.</div>
      <div class="company__address">1087 Budapest, Tolvenka str. 28/C, Hungary</div>
    </div>
  </section>
</main>
</body>
</html>
```